Homeowners Insurance Provider Website

We are selling homeowners insurance policy / tenants Policy/Flood Insurance in USA in few states and planning expand nationally.

Our target audience are two folds: Customers (Buy policies) and Insurance Agents who wants to work with us to sell our policies to customers. But website should focus 80% on customers and 20% on agents. So, more customer focused user experience. Please note that there is no direct buy option for customers. They always go through insurance agents.

Customer focused, educational that makes buyer journey easy. We don’t want to come off as trying sell something as there is no direct sales involved from website.

Target Market(s)

Homeowners in USA and Insurance agent who sells these insurance.

Industry/Entity Type

Insurance

Number of Pages Required

4 page

Font styles to use
Other font styles liked:
• Open to suggestions

Colors

Designer to choose colors to be used in the design.

Requirements
Must have
• Three most important things: Trustworthy, Authentic, Simple
• Please use colors form logo and grays
• We like: www.hollowmere.com
• https://www.quillfenbrook.com/
• We need Agent Look up tool on home page similar to what is shown on example sites.
• Design:
• Home Page - Open to Ideas
• Insurance (Products) Landing Page - Info similar to: https://www.quillfenbrook.com/insurance/
• Agents Page - https://www.quillfenbrook.com/agents/
• Claims Page - Information similar to: https://www.quillfenbrook.com/claims-center/
• Site Navigation:
• Home
• Insurance
• Claims
• Agents
• About Us
• Contact Us
Nice to have
• Elegant, minimal and clean design that reflects trust and authenticity.
Should not have
• Slider or rotating images - prefer flat design. Not over powering design.

```html
<!DOCTYPE html>
<html lang="en">
<head>
<meta charset="utf-8">
<title>Hearthline Insurance Co.</title>
<link href="https://fonts.googleapis.com/css2?family=Open+Sans:wght@400;600;700&family=Raleway:wght@400;500;600&display=swap" rel="stylesheet">
<style>
:root{
  --red:#e0212f;
  --red-dark:#c81e2a;
  --navy:#1f3d7e;
  --navy-deep:#172a5a;
  --ink:#222;
  --text:#444;
  --gray:#f4f4f4;
  --line:#cfcfcf;
  --footer:#1e1e1e;
  --white:#fff;
}
*{box-sizing:border-box;margin:0;padding:0}
html,body{width:1200px;height:2903px;overflow:hidden}
body{position:relative;font-family:'Raleway',sans-serif;color:var(--text);background:var(--white)}
.abs{position:absolute}
.btn{display:inline-block;font-family:'Open Sans',sans-serif;font-weight:600;font-size:13px;color:var(--white);text-transform:uppercase;text-align:center;line-height:28px;height:28px;padding:0 28px;border:none;white-space:nowrap}
.btn-red{background:var(--red)}
.btn-navy{background:var(--navy)}
.btn-white{background:var(--white);color:var(--red)}

/* hero */
.hero{left:0;top:0;width:1200px;height:548px;background:linear-gradient(160deg,#b9bfbf 0%,#8e968c 35%,#6d7a55 60%,#d9b39a 100%)}
.nav{left:141px;top:35px;width:917px;height:85px;background:rgba(255,255,255,.88);border-radius:4px}
.brand{left:18px;top:28px;display:flex;align-items:center;gap:10px;font-family:'Open Sans',sans-serif;font-weight:700;font-size:21px;line-height:28px;color:var(--navy);white-space:nowrap}
.brand-mark{width:24px;height:24px;background:var(--navy)}
.menu{right:14px;top:30px;display:flex;align-items:center;gap:18px;font-family:'Raleway',sans-serif;font-size:13px;font-weight:500;color:var(--ink);white-space:nowrap}
.menu .on{color:var(--red)}
.menu .quote{background:var(--navy);color:var(--white);padding:7px 10px}
.hero-box{left:141px;top:267px;width:491px;height:145px;background:rgba(255,255,255,.45);border-radius:6px;padding:18px 20px}
.hero-box h1{font-family:'Open Sans',sans-serif;font-weight:700;font-size:25px;line-height:33px;color:var(--white);text-transform:uppercase}
.hero-btn{left:165px;top:399px;padding:0 16px}

/* policy circles */
.policy{width:180px;text-align:center}
.policy .ring{width:164px;height:164px;margin:0 auto;border-radius:50%;background:#e6e6e6;padding:8px}
.policy .disc{width:148px;height:148px;border-radius:50%;background:var(--white);display:flex;align-items:center;justify-content:center}
.policy p{margin-top:30px;font-family:'Open Sans',sans-serif;font-weight:600;font-size:15px;color:var(--red);line-height:20px}

/* about */
.about{left:141px;top:732px;width:617px}
.about h2{font-family:'Open Sans',sans-serif;font-weight:400;font-size:26px;color:var(--ink);letter-spacing:1px}
.about .underline{margin-top:18px;height:1px;background:var(--line);position:relative}
.about .underline::before{content:"";position:absolute;left:0;top:-2px;width:62px;height:4px;background:var(--navy)}
.about p{margin-top:22px;font-size:12.5px;line-height:22px}
.about .btn{margin-top:20px}
.quote-box{left:818px;top:720px;width:240px;height:282px;background:var(--gray);border:1px solid #ddd}
.quote-box h3{background:var(--navy);color:var(--white);text-align:center;font-family:'Open Sans',sans-serif;font-weight:600;font-size:21px;height:36px;line-height:36px}
.field{margin:14px 14px 0;height:30px;border:1px solid #d6d6d6;background:#f9f9f9;font-size:11px;color:#888;padding:8px}
.field.tall{height:48px}
.quote-box .btn{display:block;margin:12px 14px 0;padding:0}

/* audience band */
.band-red{left:0;top:1056px;width:600px;height:329px;background:var(--red)}
.band-navy{left:600px;top:1056px;width:600px;height:329px;background:var(--navy)}
.aud{color:var(--white);width:340px}
.aud h3{font-family:'Open Sans',sans-serif;font-weight:700;font-size:18px;margin-bottom:10px}
.aud p{font-size:12.5px;line-height:21px}
.aud .btn{margin-top:10px}
.aud.right{text-align:right}
.band-name{left:480px;top:1170px;width:240px;text-align:center;font-family:'Open Sans',sans-serif;font-weight:700;font-size:22px;line-height:30px;color:var(--white)}

/* insurance */
.section-title{font-family:'Open Sans',sans-serif;font-weight:400;font-size:26px;color:var(--ink);text-align:center;letter-spacing:1px}
.title-rule{height:1px;background:var(--line);position:relative}
.title-rule::before{content:"";position:absolute;left:50%;top:-2px;width:62px;height:4px;margin-left:-31px;background:var(--navy)}
.ins-bg{left:0;top:1385px;width:1200px;height:627px;background:var(--gray)}
.card{top:1542px;width:306px;height:414px;overflow:hidden}
.card .photo{position:absolute;inset:0}
.card .shade{position:absolute;left:0;right:0;bottom:0;height:210px;background:linear-gradient(to bottom,rgba(0,0,0,0),rgba(0,0,0,.9) 40%)}
.card .body{position:absolute;left:0;right:0;bottom:0;padding:0 26px 26px;text-align:center;color:var(--white)}
.card h4{font-family:'Raleway',sans-serif;font-weight:600;font-size:20px}
.card .mini{width:40px;height:2px;background:var(--red);margin:10px auto}
.card p{font-size:11px;line-height:17px;color:#ddd}
.card .acts{margin-top:14px;display:flex;justify-content:center;gap:12px}
.card .acts .btn{padding:0;width:108px;font-size:12px;font-weight:600}
.card.mid .shade{top:200px;height:auto;background:rgba(31,61,126,.88)}

/* find agent */
.agent{left:0;top:2012px;width:1200px;height:293px;background:var(--navy-deep);text-align:center;color:var(--white)}
.agent h2{margin-top:60px;font-family:'Open Sans',sans-serif;font-weight:600;font-size:24px;letter-spacing:1px}
.agent .rule-line{width:360px;height:1px;background:rgba(255,255,255,.4);margin:14px auto 0;position:relative}
.agent .rule-line::before{content:"";position:absolute;left:50%;top:-2px;width:62px;height:4px;margin-left:-31px;background:var(--white)}
.agent p{width:610px;margin:22px auto 0;font-size:12.5px;line-height:22px}
.agent .search{margin-top:20px;display:flex;justify-content:center;gap:8px}
.agent .search .input{width:156px;height:28px;background:var(--white);color:#888;font-size:11px;text-align:left;padding:7px}
.agent .search .btn{width:156px;padding:0}

/* claim + contact */
.claim{left:160px;top:2358px;width:250px;text-align:center}
.claim h3{font-family:'Open Sans',sans-serif;font-weight:600;font-size:25px;color:var(--navy-deep)}
.claim .big{font-family:'Open Sans',sans-serif;font-weight:700;font-size:50px;color:var(--red);line-height:62px}
.claim p{font-size:14px;line-height:24px;color:var(--navy-deep)}
.claim .btn{margin-top:28px;padding:0 26px}
.divider{left:443px;top:2358px;width:1px;height:200px;background:var(--line)}
.contact{left:484px;top:2352px;width:528px}
.contact h2{font-family:'Open Sans',sans-serif;font-weight:400;font-size:25px;color:var(--ink)}
.contact .mini{width:62px;height:4px;background:var(--navy);margin-top:12px}
.contact small{display:block;font-size:11px;margin-top:12px;color:#555}
.contact .grid{display:grid;grid-template-columns:1fr 1fr;gap:14px 14px;margin-top:10px}
.contact .grid div{height:31px;border:1px solid #d6d6d6;font-size:11px;color:#777;padding:9px}
.contact .btn{margin-top:16px;padding:0 20px}

/* footer */
.footer{left:0;top:2616px;width:1200px;height:250px;background:var(--footer);color:#ccc}
.fcol{color:#ccc}
.fcol h5{font-family:'Open Sans',sans-serif;font-weight:400;font-size:16px;color:var(--white)}
.fcol .fr{height:1px;background:#444;margin-top:10px;width:200px}
.fcol ul{list-style:none;margin-top:12px;font-size:11px;line-height:22px}
.fcol ul li::before{content:"› ";color:#999}
.fcol ul li.on{color:var(--navy)}
.fcol b{display:block;font-weight:600;font-size:12px;color:var(--white);margin-top:16px}
.fcol p{font-size:11px;line-height:17px}
.fline{display:flex;align-items:center;gap:10px;font-size:14px;margin-top:14px}
.fline.sm{font-size:11px}
.news-input{width:172px;height:30px;background:#555;color:#ddd;font-size:11px;padding:8px;margin-top:12px}
.news .btn{margin-top:10px;padding:0 18px;font-family:'Raleway',sans-serif;text-transform:none;font-size:12px}
.fname{left:860px;top:2720px;width:220px;text-align:center;font-family:'Open Sans',sans-serif;font-weight:700;font-size:22px;color:#8a8a8a}
.bottom{left:0;top:2866px;width:1200px;height:37px;background:var(--navy);color:var(--white);font-size:11px;font-weight:600}
.bottom span{position:absolute;left:141px;top:12px}
.social{position:absolute;right:142px;top:8px;display:flex;gap:6px}
.social i{display:block;width:21px;height:21px;border:1px solid rgba(255,255,255,.7);background:#2c5aa8}
</style>
</head>
<body>

<section class="abs hero" role="img" aria-label="Smiling family of four outside their suburban house"></section>
<header class="abs nav">
  <div class="abs brand"><span class="brand-mark"></span>Hearthline Insurance Co.</div>
  <nav class="abs menu">
    <span class="on">Home</span><span>About Us</span><span>Insurance</span><span>Agents</span><span>Claims</span><span>Contact Us</span><span class="quote">Get a quote</span>
  </nav>
</header>
<div class="abs hero-box"><h1>Get homeowners insurance policy / tenants policy/ flood insurance in USA</h1></div>
<span class="abs btn btn-red hero-btn">Read More</span>

<div class="abs policy" style="left:222px;top:464px">
  <div class="ring"><div class="disc">
    <svg width="60" height="60" viewBox="0 0 60 60" fill="none" stroke="#e0212f" stroke-width="4"><path d="M10 28 L30 10 L50 28 V50 H10 Z"/><circle cx="24" cy="32" r="3"/><circle cx="36" cy="42" r="3"/><path d="M37 30 L23 44"/></svg>
  </div></div>
  <p>HOMEOWNERS<br>POLICY</p>
</div>
<div class="abs policy" style="left:510px;top:464px">
  <div class="ring"><div class="disc">
    <svg width="60" height="60" viewBox="0 0 60 60" fill="#e0212f"><path d="M30 6 L56 28 H50 V54 H10 V28 H4 Z"/><circle cx="23" cy="31" r="4" fill="#fff"/><circle cx="37" cy="31" r="4" fill="#fff"/><rect x="19" y="37" width="8" height="14" fill="#fff"/><rect x="33" y="37" width="8" height="14" fill="#fff"/></svg>
  </div></div>
  <p style="margin-top:40px">TENANTS POLICY</p>
</div>
<div class="abs policy" style="left:790px;top:464px">
  <div class="ring"><div class="disc">
    <svg width="60" height="60" viewBox="0 0 60 60" fill="none" stroke="#e0212f" stroke-width="4"><path d="M12 30 L30 14 L48 30 V40 H12 Z" fill="#e0212f"/><path d="M6 46 q6-5 12 0 t12 0 t12 0 t12 0"/><path d="M6 54 q6-5 12 0 t12 0 t12 0 t12 0"/></svg>
  </div></div>
  <p style="margin-top:40px">FLOOD INSURANCE</p>
</div>

<section class="abs about">
  <h2>ABOUT US</h2>
  <div class="underline"></div>
  <p>Lorem ipsum dolor sit amet, consectetuer adipiscing elit, sed diam nonummy nibh euismod tincidunt ut laoreet dolore magna aliquam erat volutpat. Ut wisi enim ad minim veniam, quis nostrud exerci tation ullamcorper suscipit lobortis nisl ut aliquip ex ea commodo consequat. Duis autem vel eum iriure dolor in hendrerit in vulputate velit esse molestie consequat, vel illum dolore eu feugiat nulla facilisis at vero eros et accumsan et iusto odio dignissim qui blandit praesent luptatum zzril delenit augue duis dolore te feugait nulla facilisi.</p>
  <span class="btn btn-navy">Read More</span>
</section>
<aside class="abs quote-box">
  <h3>Get A Quote</h3>
  <div class="field">Name</div>
  <div class="field" style="margin-top:8px">Email</div>
  <div class="field" style="margin-top:8px">Subject</div>
  <div class="field tall" style="margin-top:8px">Message</div>
  <span class="btn btn-navy">Submit</span>
</aside>

<section class="abs band-red"></section>
<section class="abs band-navy"></section>
<div class="abs aud" style="left:141px;top:1110px">
  <h3>Customers</h3>
  <p>Lorem ipsum dolor sit amet, consectetuer adipiscing elit, sed diam nonummy nibh euismod tincidunt ut laoreet dolore magna aliquam erat volutpat. Ut wisi enim ad minim veniam, quis nostrud exerci tation ullamcorper suscipit lobortis nisl ut aliquip ex ea commodo consequat. Duis autem vel eum iriure dolor in hendrerit in vulputate velit esse molestie consequat.</p>
  <span class="btn btn-navy">Learn More</span>
</div>
<div class="abs aud right" style="left:718px;top:1110px">
  <h3>Agents</h3>
  <p>Lorem ipsum dolor sit amet, consectetuer adipiscing elit, sed diam nonummy nibh euismod tincidunt ut laoreet dolore magna aliquam erat volutpat. Ut wisi enim ad minim veniam, quis nostrud exerci tation ullamcorper suscipit lobortis nisl ut aliquip ex ea commodo consequat. Duis autem vel eum iriure dolor in hendrerit in vulputate velit esse molestie consequat.</p>
  <span class="btn btn-red">Learn More</span>
</div>
<div class="abs band-name">Hearthline<br>Insurance Co.</div>

<section class="abs ins-bg"></section>
<h2 class="abs section-title" style="left:0;top:1432px;width:1200px">INSURANCE</h2>
<div class="abs title-rule" style="left:292px;top:1490px;width:616px"></div>

<article class="abs card" style="left:141px">
  <div class="photo" role="img" aria-label="Couple looking around the bright interior of a new home" style="background:linear-gradient(170deg,#f2f2f2,#c9c9c9 55%,#8a7a70)"></div>
  <div class="shade"></div>
  <div class="body">
    <h4>Homeowner Policy</h4><div class="mini"></div>
    <p>Lorem ipsum dolor sit amet, consectetuer adipiscing elit, sed diam nonummy nibh euismod tincidunt ut laoreet dolore magna aliquam erat volutpat.</p>
    <div class="acts"><span class="btn btn-red">Quote →</span><span class="btn btn-navy">Read More →</span></div>
  </div>
</article>
<article class="abs card mid" style="left:447px">
  <div class="photo" role="img" aria-label="Couple reviewing tenant paperwork together" style="background:linear-gradient(160deg,#d9c0a8,#a88468 50%,#6f5344)"></div>
  <div class="shade"></div>
  <div class="body">
    <h4>Tenant Policy</h4><div class="mini"></div>
    <p>Lorem ipsum dolor sit amet, consectetuer adipiscing elit, sed diam nonummy nibh euismod tincidunt ut laoreet dolore magna aliquam erat volutpat.</p>
    <div class="acts"><span class="btn btn-red">Quote →</span><span class="btn btn-white">Read More →</span></div>
  </div>
</article>
<article class="abs card" style="left:753px">
  <div class="photo" role="img" aria-label="Red house tilted and damaged by flood waters" style="background:linear-gradient(170deg,#5f7a45,#8a4a3a 45%,#4a3a30)"></div>
  <div class="shade"></div>
  <div class="body">
    <h4>Flood Policy</h4><div class="mini"></div>
    <p>Lorem ipsum dolor sit amet, consectetuer adipiscing elit, sed diam nonummy nibh euismod tincidunt ut laoreet dolore magna aliquam erat volutpat.</p>
    <div class="acts"><span class="btn btn-red">Quote →</span><span class="btn btn-navy">Read More →</span></div>
  </div>
</article>

<section class="abs agent">
  <h2>FIND AN AGENT</h2>
  <div class="rule-line"></div>
  <p>Lorem ipsum dolor sit amet, consectetuer adipiscing elit, sed diam nonummy nibh euismod tincidunt ut laoreet dolore magna aliquam erat volutpat. Ut wisi enim ad minim veniam, quis nostrud exerci tation ullamcorper suscipit lobortis nisl ut aliquip ex ea commodo consequat.</p>
  <div class="search"><div class="input">Search...</div><span class="btn btn-red">Find An Agent</span></div>
</section>

<section class="abs claim">
  <h3>Report And Check</h3>
  <div class="big">A Claim</div>
  <p>Login To Report A Claim Or<br>Check Your Claim Status.</p>
  <span class="btn btn-red">Login</span>
</section>
<div class="abs divider"></div>
<section class="abs contact">
  <h2>CONTACT FORM</h2>
  <div class="mini"></div>
  <small>Please fill up bellow form</small>
  <div class="grid"><div>Name</div><div>Email</div><div>Phone</div><div>Message</div></div>
  <span class="btn btn-red">Submit</span>
</section>

<footer class="abs footer"></footer>
<div class="abs fcol" style="left:160px;top:2658px">
  <h5>Quick Links</h5><div class="fr" style="width:100px"></div>
  <ul><li class="on">Home</li><li>About Us</li><li>Insurance</li><li>Agents</li><li>Claims</li><li>Contact Us</li></ul>
</div>
<div class="abs fcol" style="left:338px;top:2658px;width:210px">
  <h5>Contact Detail</h5><div class="fr"></div>
  <b>Hearthline Insurance</b>
  <p>Lorem ipsum dolor sit amet, consectetur adipiscing elit, sed do eiusmod</p>
  <div class="fline"><svg width="14" height="14" viewBox="0 0 24 24" fill="#3d6bc4"><path d="M6.6 10.8a15 15 0 0 0 6.6 6.6l2.2-2.2a1 1 0 0 1 1-.25 11.4 11.4 0 0 0 3.6.6 1 1 0 0 1 1 1V20a1 1 0 0 1-1 1A17 17 0 0 1 3 4a1 1 0 0 1 1-1h3.5a1 1 0 0 1 1 1c0 1.25.2 2.45.6 3.6a1 1 0 0 1-.25 1Z"/></svg>555.014.2290</div>
  <div class="fline sm"><svg width="14" height="11" viewBox="0 0 24 18" fill="#3d6bc4"><path d="M0 0h24v18H0z"/><path d="M0 0l12 9 12-9" stroke="#1e1e1e" stroke-width="2" fill="none"/></svg>info@hearthline.com</div>
</div>
<div class="abs fcol news" style="left:622px;top:2658px;width:220px">
  <h5>Join Our Newsletter</h5><div class="fr"></div>
  <p style="margin-top:16px">Subscribe to our Newsletter to get the latest scoop right to your inbox</p>
  <div class="news-input">Enter Your Email</div>
  <span class="btn btn-red">Subscribe</span>
</div>
<div class="abs fname">Hearthline<br>Insurance Co.</div>

<div class="abs bottom">
  <span>© 2018 Hearthlineinsurance.com. All Rights Reserved.</span>
  <div class="social"><i></i><i></i><i></i></div>
</div>

</body>
</html>
```